Modern Label for cleaning products for the brand Vorlix

We need a label design for our line of cleaning products. The label should feature our logo and an image to identify the product's intended use. I've added our logo and an image for use. This only concerns the design of the label on the front of the bottle.

Label dimensions:
Label 1 (500ml bottle with spray): width 58mm x height 115mm
Label 2: (1L bottle): width 73mm x height 140mm
The design must be consistent for both bottles which you find in the pictures.

The bottles to be labeled are white. See the attachment for a photo of the bottles.

The photo must also appear on the label to identify the product's intended use.

Product information:
Brand: Vorlix
Product: Sanitary Cleaner

This text must be placed on the label:
"Cleans, descales & freshens. followed with this text: "Ideal for quick and powerful cleaning. A ready-to-use product for everyday use."

- Mention the seperate USP's: Sanitary, Bathroom, Toilet, Wet areas

Appearance: This is a consumer product, but it must have a professional appearance. We would like to see a design that use the color blue from our logo.

Target Market(s)

Consumers who take care of their homes and want to maintain it the correct (professional) way

Font styles to use
Sans Serif

Colors
0054AA
0677BA
7BADD7
CADEEF
E8F1F8

Requirements
Must have
• USP's + use of image and logo + blend in 1 design
Nice to have
• Keep the color of the logo in the design
Should not have
• Comic sans

```html
<!DOCTYPE html>
<html lang="en">
<head>
<meta charset="utf-8">
<title>Vorlix Sanitary Cleaner – Bottle Labels</title>
<link rel="stylesheet" href="https://fonts.googleapis.com/css2?family=Poppins:ital,wght@0,400;0,600;0,700;0,800;1,800&display=swap">
<style>
  :root{
    --ink:#1b1b1b;
    --brand-blue:#0a5db2;
    --bright-blue:#00adef;
    --navy:#003366;
    --navy-mid:#00589f;
    --white:#ffffff;
    --photo-light:#e6e8ea;
    --photo-mid:#b9b6b2;
    --photo-dark:#8f8b87;
  }
  html,body{margin:0;padding:0;overflow:hidden;}
  body{width:1200px;height:989px;background:var(--white);position:relative;font-family:"Poppins",sans-serif;}
  .label{position:absolute;display:block;}
  .label--500{left:160px;top:178px;width:341px;height:678px;}
  .label--1l{left:600px;top:77px;width:431px;height:825px;}
  .brand-name{font-family:"Poppins",sans-serif;font-weight:700;fill:var(--ink);}
  .title{font-family:"Poppins",sans-serif;font-weight:800;fill:var(--brand-blue);}
  .subtitle{font-family:"Poppins",sans-serif;font-weight:700;fill:var(--bright-blue);}
  .usp{font-family:"Poppins",sans-serif;font-weight:400;fill:var(--white);}
  .claim{font-family:"Poppins",sans-serif;font-weight:800;font-style:italic;fill:var(--white);}
  .benefit{font-family:"Poppins",sans-serif;font-weight:700;fill:var(--white);}
  .pill-text{font-family:"Poppins",sans-serif;font-weight:600;fill:var(--white);}
  .volume{font-family:"Poppins",sans-serif;font-weight:400;fill:var(--white);}
  .tick-icon{fill:none;stroke:var(--white);stroke-width:2.6;stroke-linecap:round;stroke-linejoin:round;}
</style>
</head>
<body>

<!-- 500 ml label -->
<svg class="label label--500" viewBox="0 0 605 1202" aria-label="Vorlix Sanitary Cleaner 500 ml label">
  <defs>
    <clipPath id="shape-500">
      <path d="M1,95 Q1,32 60,22 Q302,-16 545,22 Q604,32 604,95 V1140 Q604,1200 545,1200 H60 Q1,1200 1,1140 Z"/>
    </clipPath>
    <linearGradient id="panel-500" x1="0" y1="0" x2="0" y2="1">
      <stop offset="0" stop-color="var(--navy-mid)"/>
      <stop offset="0.35" stop-color="var(--navy)"/>
      <stop offset="1" stop-color="var(--navy)"/>
    </linearGradient>
    <linearGradient id="photo-500" x1="0" y1="0" x2="1" y2="1">
      <stop offset="0" stop-color="var(--photo-dark)"/>
      <stop offset="0.45" stop-color="var(--photo-light)"/>
      <stop offset="1" stop-color="var(--photo-mid)"/>
    </linearGradient>
  </defs>
  <g clip-path="url(#shape-500)">
    <rect width="605" height="1202" fill="var(--white)"/>
    <rect class="photo" role="img" aria-label="Photo of a clean modern bathroom with walk-in shower, washbasin and bathtub" x="0" y="410" width="605" height="460" fill="url(#photo-500)"/>
    <path d="M0,420 Q302,535 605,420 V0 H0 Z" fill="var(--white)"/>
    <path d="M0,405 Q302,505 605,405 V422 Q302,535 0,422 Z" fill="var(--navy)"/>
    <path d="M0,845 Q302,760 605,845 V1202 H0 Z" fill="var(--bright-blue)"/>
    <path d="M0,860 Q302,782 605,860 V1202 H0 Z" fill="url(#panel-500)"/>
  </g>
  <path d="M1,95 Q1,32 60,22 Q302,-16 545,22 Q604,32 604,95 V1140 Q604,1200 545,1200 H60 Q1,1200 1,1140 Z" fill="none" stroke="var(--ink)" stroke-width="2"/>

  <circle cx="302" cy="88" r="50" fill="none" stroke="var(--brand-blue)" stroke-width="11"/>
  <text class="brand-name" x="302" y="185" font-size="58" text-anchor="middle">Vorlix</text>

  <text class="title" x="302" y="325" font-size="94" text-anchor="middle" textLength="482" lengthAdjust="spacingAndGlyphs">SANITARY</text>
  <text class="subtitle" x="302" y="391" font-size="62" text-anchor="middle" textLength="355" lengthAdjust="spacing">CLEANER</text>

  <g class="tick-icon">
    <circle cx="108" cy="886" r="14"/><path d="M101,886 l5,6 l10,-13"/>
    <circle cx="314" cy="886" r="14"/><path d="M307,886 l5,6 l10,-13"/>
    <circle cx="132" cy="937" r="14"/><path d="M125,937 l5,6 l10,-13"/>
    <circle cx="284" cy="937" r="14"/><path d="M277,937 l5,6 l10,-13"/>
  </g>
  <text class="usp" x="127" y="900" font-size="37">Sanitary</text>
  <text class="usp" x="334" y="900" font-size="37">Bathroom</text>
  <text class="usp" x="152" y="951" font-size="37">Toilet</text>
  <text class="usp" x="305" y="951" font-size="37">Wet Areas</text>

  <text class="claim" x="302" y="1020" font-size="30" text-anchor="middle" textLength="488" lengthAdjust="spacingAndGlyphs">CLEANS, DESCALES &amp; FRESHENS</text>
  <text class="benefit" x="302" y="1058" font-size="23" text-anchor="middle" textLength="526" lengthAdjust="spacingAndGlyphs">IDEAL FOR QUICK AND POWERFUL CLEANING</text>

  <rect x="29" y="1082" width="546" height="30" rx="15" fill="var(--bright-blue)"/>
  <text class="pill-text" x="302" y="1104" font-size="18" text-anchor="middle" textLength="500" lengthAdjust="spacing">A READY-TO-USE PRODUCT FOR EVERYDAY USE</text>

  <path d="M254,1200 V1163 Q254,1157 260,1157 H343 Q349,1157 349,1163 V1200 Z" fill="var(--bright-blue)"/>
  <text class="volume" x="302" y="1185" font-size="25" text-anchor="middle">500 ml</text>
</svg>

<!-- 1 L label -->
<svg class="label label--1l" viewBox="0 0 763 1462" aria-label="Vorlix Sanitary Cleaner 1 litre label">
  <defs>
    <clipPath id="shape-1l">
      <path d="M1,115 Q1,40 75,26 Q381,-18 690,26 Q762,40 762,115 V1385 Q762,1460 690,1460 H75 Q1,1460 1,1385 Z"/>
    </clipPath>
    <linearGradient id="panel-1l" x1="0" y1="0" x2="0" y2="1">
      <stop offset="0" stop-color="var(--navy-mid)"/>
      <stop offset="0.35" stop-color="var(--navy)"/>
      <stop offset="1" stop-color="var(--navy)"/>
    </linearGradient>
    <linearGradient id="photo-1l" x1="0" y1="0" x2="1" y2="1">
      <stop offset="0" stop-color="var(--photo-dark)"/>
      <stop offset="0.45" stop-color="var(--photo-light)"/>
      <stop offset="1" stop-color="var(--photo-mid)"/>
    </linearGradient>
  </defs>
  <g clip-path="url(#shape-1l)">
    <rect width="763" height="1462" fill="var(--white)"/>
    <rect class="photo" role="img" aria-label="Photo of a clean modern bathroom with walk-in shower, washbasin and bathtub" x="0" y="470" width="763" height="580" fill="url(#photo-1l)"/>
    <path d="M0,483 Q381,610 763,483 V0 H0 Z" fill="var(--white)"/>
    <path d="M0,462 Q381,585 763,462 V483 Q381,612 0,483 Z" fill="var(--navy)"/>
    <path d="M0,1012 Q381,905 763,1012 V1462 H0 Z" fill="var(--bright-blue)"/>
    <path d="M0,1030 Q381,930 763,1030 V1462 H0 Z" fill="url(#panel-1l)"/>
  </g>
  <path d="M1,115 Q1,40 75,26 Q381,-18 690,26 Q762,40 762,115 V1385 Q762,1460 690,1460 H75 Q1,1460 1,1385 Z" fill="none" stroke="var(--ink)" stroke-width="2"/>

  <circle cx="381" cy="108" r="62" fill="none" stroke="var(--brand-blue)" stroke-width="13"/>
  <text class="brand-name" x="381" y="236" font-size="72" text-anchor="middle">Vorlix</text>

  <text class="title" x="381" y="393" font-size="120" text-anchor="middle" textLength="605" lengthAdjust="spacingAndGlyphs">SANITARY</text>
  <text class="subtitle" x="381" y="473" font-size="80" text-anchor="middle" textLength="446" lengthAdjust="spacing">CLEANER</text>

  <g class="tick-icon" style="stroke-width:3.2">
    <circle cx="137" cy="1066" r="18"/><path d="M128,1066 l6,8 l13,-17"/>
    <circle cx="395" cy="1066" r="18"/><path d="M386,1066 l6,8 l13,-17"/>
    <circle cx="167" cy="1131" r="18"/><path d="M158,1131 l6,8 l13,-17"/>
    <circle cx="358" cy="1131" r="18"/><path d="M349,1131 l6,8 l13,-17"/>
  </g>
  <text class="usp" x="162" y="1083" font-size="47">Sanitary</text>
  <text class="usp" x="422" y="1083" font-size="47">Bathroom</text>
  <text class="usp" x="193" y="1148" font-size="47">Toilet</text>
  <text class="usp" x="385" y="1148" font-size="47">Wet Areas</text>

  <text class="claim" x="381" y="1235" font-size="38" text-anchor="middle" textLength="615" lengthAdjust="spacingAndGlyphs">CLEANS, DESCALES &amp; FRESHENS</text>
  <text class="benefit" x="381" y="1283" font-size="29" text-anchor="middle" textLength="662" lengthAdjust="spacingAndGlyphs">IDEAL FOR QUICK AND POWERFUL CLEANING</text>

  <rect x="36" y="1313" width="689" height="38" rx="19" fill="var(--bright-blue)"/>
  <text class="pill-text" x="381" y="1340" font-size="23" text-anchor="middle" textLength="630" lengthAdjust="spacing">A READY-TO-USE PRODUCT FOR EVERYDAY USE</text>

  <path d="M325,1460 V1416 Q325,1408 333,1408 H427 Q435,1408 435,1416 V1460 Z" fill="var(--bright-blue)"/>
  <text class="volume" x="380" y="1444" font-size="29" text-anchor="middle">1 Lt</text>
</svg>

</body>
</html>
```